Talbrook Answering Service Brochure

Design a brochure for an answering service/call center based on the information submitted/attached. Photos and text will be included. Would like it designed to complement the logo provided. This brochure will explain to the potential customer who we are and what we have to offer.

The Talbrook representatives take and processes inbound calls, 24-7-365

Target Market(s)

Any business, however, primarily Medical, oil and gas, non profits, and the service industry

Industry/Entity Type

Telecommunications

Font styles to use
Serif
Other font styles liked:
• coordinate with logo

Requirements
Must have
• Modern, bright, bold and neatly structured brochure that will complement the logo and our brand.

```html
<!DOCTYPE html>
<html lang="en">
<head>
<meta charset="utf-8">
<title>Talbrook Answering Service Brochure</title>
<link href="https://fonts.googleapis.com/css2?family=Montserrat:wght@500;600;700&family=Lato:wght@300;400&display=swap" rel="stylesheet">
<style>
  :root {
    --red: #c81f29;
    --heading: #6e6e6e;
    --body: #4a4a4a;
    --paper: #ffffff;
    --bg: #e4e4e4;
    --slate: #2d3436;
  }
  * { margin: 0; padding: 0; box-sizing: border-box; }
  html, body { width: 1200px; height: 1200px; overflow: hidden; background: var(--bg); }
  body { position: relative; font-family: "Lato", sans-serif; color: var(--body); }
  .spread {
    position: absolute; left: 0; top: 211px; width: 1200px; height: 777px;
    background: var(--paper);
  }
  .spread > * { position: absolute; }
  .about-title {
    left: 48px; top: 30px; font-family: "Montserrat", sans-serif; font-weight: 700;
    font-size: 32px; color: var(--heading); letter-spacing: .5px;
  }
  .copy { font-size: 11.3px; line-height: 14.6px; font-weight: 400; }
  .copy p + p { margin-top: 7px; }
  .about-copy { left: 48px; top: 79px; width: 525px; }
  .teamwork-photo { left: 0; top: 246px; width: 490px; height: 302px; overflow: hidden; }
  .teamwork-photo .fill {
    position: absolute; inset: 0;
    background: linear-gradient(90deg, var(--slate) 0%, #3b4446 55%, rgba(255,255,255,0) 100%);
  }
  .teamwork-photo svg { position: absolute; inset: 0; }
  .anniversary { left: 455px; top: 368px; width: 120px; text-align: center; }
  .brand-name {
    display: flex; align-items: center; justify-content: center; gap: 5px;
    font-family: "Montserrat", sans-serif; font-weight: 700; font-size: 11px;
    color: var(--slate); line-height: 12px; text-align: left;
  }
  .brand-name .dot { width: 12px; height: 12px; border-radius: 50%; background: var(--red); flex: none; }
  .years-num {
    font-family: "Montserrat", sans-serif; font-weight: 700; font-size: 74px;
    line-height: 70px; color: #c9c9c9; margin-top: 14px;
  }
  .years-label {
    font-family: "Montserrat", sans-serif; font-weight: 700; font-size: 24px;
    color: #c9c9c9; line-height: 26px;
  }
  .section-title {
    font-family: "Montserrat", sans-serif; font-weight: 700; font-size: 21px; color: var(--heading);
  }
  .section-sub {
    font-family: "Montserrat", sans-serif; font-weight: 600; font-size: 16px; color: var(--heading);
  }
  .live-auto { left: 48px; top: 553px; width: 540px; }
  .live-auto .section-sub { margin-top: 1px; }
  .live-auto .copy { margin-top: 3px; }
  .growing { left: 48px; top: 665px; width: 540px; }
  .growing .copy { margin-top: 6px; }
  .label {
    background: var(--red); color: #fff; font-family: "Montserrat", sans-serif; font-weight: 600;
    font-size: 13px; height: 28px; line-height: 28px; padding-left: 11px;
  }
  .label-live { left: 649px; top: 35px; width: 221px; }
  .label-auto { left: 649px; top: 248px; width: 227px; }
  .label-any { left: 649px; top: 603px; width: 230px; }
  .live-copy { left: 649px; top: 84px; width: 245px; }
  .bullets { list-style: none; }
  .bullets li { position: relative; padding-left: 13px; }
  .bullets li::before {
    content: ""; position: absolute; left: 2px; top: 5.5px; width: 4px; height: 4px;
    border-radius: 50%; background: #8a8a8a;
  }
  .bullets .note { padding-left: 13px; }
  .bullets .note::before { display: none; }
  .live-list { left: 921px; top: 84px; width: 260px; line-height: 15.7px; }
  .auto-copy { left: 649px; top: 296px; width: 520px; }
  .auto-lead { left: 649px; top: 366px; width: 360px; font-weight: 400; color: #222; }
  .auto-list { left: 649px; top: 402px; width: 520px; line-height: 15.7px; }
  .any-copy { left: 649px; top: 653px; width: 480px; }
</style>
</head>
<body>
<main class="spread">
  <h1 class="about-title">ABOUT US</h1>
  <div class="copy about-copy">
    <p>Talbrook, over the past 84 years, has operated through wars, floods and hurricanes. Our long history is important as it shows Consistency, Professionalism, Experience, and a Can Do Attitude, which is hard to find in the answering service industry today.</p>
    <p>At Talbrook, you’ll never be just another a number. We will become part of YOUR team on day one and remain there, ready and honored to serve by providing reliable, professional answering services, 24-7-365, as needed.</p>
    <p>Talbrook Answering Service is your award winning, five start center, backed by critical redundancy and a solid infrastructure, for the highest availability possible.</p>
  </div>

  <div class="teamwork-photo" role="img" aria-label="Photo of a team around a chalkboard drawn with gears and the words teamwork, goals, success, vision and skills">
    <div class="fill"></div>
    <svg width="490" height="302" viewBox="0 0 490 302" aria-hidden="true">
      <path d="M0,198 Q210,282 490,302 L0,302 Z" fill="#c81f29"/>
      <path d="M0,224 Q200,292 490,302 L0,302 Z" fill="#ffffff"/>
    </svg>
  </div>

  <div class="anniversary">
    <div class="brand-name"><span class="dot"></span><span>TALBROOK<br>ANSWERING SERVICE</span></div>
    <div class="years-num">84</div>
    <div class="years-label">YEARS</div>
  </div>

  <section class="live-auto">
    <h2 class="section-title">LIVE OR AUTOMATED</h2>
    <h3 class="section-sub">Answering Services That Work for You</h3>
    <p class="copy">Tell us about your needs and your budget and we’ll do the rest. Talbrook selects a system that satisfies your basic requirements, then evaluates your business to find a long-term solution that will work for you and your customers.</p>
  </section>

  <section class="growing">
    <h3 class="section-sub">Still Growing? Find a Scalable Phone Answering Service</h3>
    <p class="copy">A scalable solution is one that doesn’t waste resources when you don’t need them, but easily adapts to future growth. All of our services at Talbrook grow with you, meaning you don’t pay for additional support until you need it.</p>
  </section>

  <h2 class="label label-live">Live Answering Service</h2>
  <p class="copy live-copy">Talbrook is more than an answering service, it’s an extension of your company. Our professional representatives take pride in being your direct line of communication with existing customers, potential customers, and valued business partners. Before we start fielding calls, our representatives are trained according to the details of your business.</p>
  <ul class="copy bullets live-list">
    <li>24 Hour Answering Service</li>
    <li>Virtual Receptionist / Virtual Assistant</li>
    <li>Live Message Relay</li>
    <li>Help Desk Overflow</li>
    <li>Call Screening</li>
    <li>Bilingual Answering (English/Spanish)</li>
  </ul>

  <h2 class="label label-auto">Automated Services</h2>
  <p class="copy auto-copy">Live answering services are not necessary for all businesses. Talbrook offers automated answering services as a cost-effective option for continuous customer contact.<br>All automated service solutions can be built and customized to fit your specific business.<br>( Live and automated services can be combined for a very cost effective and professional solution.)</p>
  <p class="copy auto-lead">Here are some of the customizable automated solutions we offer for businesses of all sizes:</p>
  <ul class="copy bullets auto-list">
    <li>Voice Mail (with or without extensions/sub-boxes)</li>
    <li>Call Routing &amp; Transfer</li>
    <li>Web Integration</li>
    <li>Database Interaction</li>
    <li>Text Messaging</li>
    <li>Email</li>
    <li>Fax</li>
    <li>Voice Mail with Operator Revert</li>
    <li class="note">Combination Service – Utilize our reliable voice mail system with an operator revert functionality. Your callers have the option of pressing “0” for a representative at any time.</li>
  </ul>

  <h2 class="label label-any">Any Call - Any Time - Any Place</h2>
  <p class="copy any-copy">Talbrook serves many various types of industries, and businesses of all sizes, including the one person start up and the Fortune 500 company needing daytime overflow assistance or after hour emergency dispatch. If your business depends on successful processing of your inbound calls, you can benefit from the experienced team at Talbrook.</p>
</main>
</body>
</html>
```